Residential Mortgage Leader needs Wordpress Design

Looking for a home page website design for a client. We develop using the WordPress platform and would prefer the design be at least loosely based on an existing WordPress template. Attached files have many notes from our creative brief with client. The site must be responsive. Approved, basic wireframe attached. There is room for interpretation.

Existing web site: http://www.marisolkettering.example/

The Marisol Kettering Team relies on strong systems to deliver an on-time, done-right, friendly experience. Marisol offers mortgages and refinancing services throughout the United States. She is a successful Brookvale Funding agent who strives to be an active part of her community. She would like to focus the site on her team, rather than just her.

Difference makers...
When you work with the Marisol Kettering team you get a high level of expertise and a friendly experience.

She has amazing credentials. Marisol is widely recognized as a top producer for her company, and has earned a number of awards and honors for her customer service.

Marisol's team is very engaged and enjoys sharing social comments or photos from their community.

Imagery:
* Friendly, warm imagery, preferably of her team or an image to represent her team
* Clean and crisp
* Professional / Experts in mortgage and refinance
* Clean / Good use of white space
Updates

When possible, please use imagery from the DFW area. The client mentioned they would prefer not to see stock images. Thanks.

Amend that- creative use of stock images, however, is fine. A few designs have used stock imagery, but in a well-considered manner.

We added some photos and graphics that are local. We are Dallas / Ft. Worth, Plano, Frisco, Texas. We also added some examples of photos to use for the "In the Community" area. Stock photos of business folks just doesn't fit there. Thanks!

Target Market(s)

They service a lot of builders, but also work with homeowners. Their typical client is usually a woman searching for mortgage services online. She typically has a family and may refer her husband to Marisol's team. Keep in mind, however, they also see a number of other scenarios. Most of their clients are middle to high-end borrowers.

Industry/Entity Type

It Company

Requirements
Must have
• Design should be developed using program such as Photoshop or Fireworks or Illustrator as last preference. Ideally, the design would be based on an existing responsive WordPress theme, which we would customize. You must include the name of the target theme. The footer should include lots of space for disclaimers and legal language. Site navigation should include these choices: "Home, About, Builders, Mortgage Info, Approval, Blog, Contact"
Nice to have
• Blog, social media and photos area. Use of the already approved style prototype with colors and fonts (Lato- a Google font, Times New Roman and Cookie-a decorative Google font). However, we are open to interpretation.
Should not have
• Hard to read fonts or a lack of white space.

```html
<!DOCTYPE html>
<html lang="en">
<head>
<meta charset="utf-8">
<title>Marisol Kettering Team</title>
<link href="https://fonts.googleapis.com/css2?family=Lato:wght@300;400;700&display=swap" rel="stylesheet">
<style>
:root{
  --red:#b3191b;
  --ink:#3a3a3a;
  --muted:#777;
  --rule:#e2e2e2;
  --page:#efefef;
  --nav:#2f2f2f;
  --foot:#353535;
  --foot-deep:#2b2b2b;
  --link:#1ba0c8;
}
*{box-sizing:border-box;margin:0;padding:0}
html,body{width:797px;height:1200px;overflow:hidden}
body{background:var(--page);font-family:'Lato',sans-serif;color:var(--ink);position:relative}
.sheet{position:absolute;left:73px;top:0;width:651px;height:1200px;background:#fff;border-top:3px solid var(--nav)}
.abs{position:absolute}

/* header */
.brand{left:9px;top:25px;font-size:16px;line-height:18px;color:var(--red);letter-spacing:-.2px;white-space:nowrap}
.brand-sub{left:9px;top:44px;font-size:5.5px;color:#999;letter-spacing:.5px;text-transform:uppercase;white-space:nowrap}
.partner{left:150px;top:27px;display:flex;align-items:center;gap:5px;white-space:nowrap}
.partner b{font-size:11px;color:var(--red);font-weight:700}
.partner i{width:12px;height:12px;background:var(--red);display:block}
.partner-sub{left:150px;top:42px;font-size:5.5px;color:#444;white-space:nowrap}
.contact{right:9px;top:19px;font-size:10px;color:#999;line-height:15px;text-align:right}
.contact span{display:flex;align-items:center;gap:6px;justify-content:flex-end}
.contact svg{width:8px;height:8px;fill:#888}

/* nav */
.nav{left:0;top:70px;width:651px;height:34px;background:var(--nav);display:flex}
.nav a{color:#fff;font-size:8px;text-decoration:none;text-transform:uppercase;height:34px;line-height:34px;padding:0 13.5px;border-right:1px solid #444}
.nav a:first-child{padding-left:20px}
.nav-social{position:absolute;right:10px;top:12px;display:flex;gap:9px}
.nav-social i{width:9px;height:9px;border:1.5px solid #bbb;display:block}

/* hero */
.hero{left:0;top:121px;width:651px;height:380px;background:linear-gradient(100deg,#8d99a6 0%,#c9d3dc 30%,#e9ecef 55%,#b9c1c9 75%,#d4d9de 100%)}
.hero-title{left:180px;top:114px;width:298px;height:36px;background:#fff;text-align:center;font-size:25px;line-height:36px;color:#444;font-weight:400}
.hero-text{left:180px;top:155px;width:298px;height:61px;background:#fff;text-align:center;font-size:12.2px;line-height:17px;padding:5px 30px 0;color:#444}
.btn{top:230px;height:25px;line-height:25px;color:#fff;font-size:11px;text-align:center;border-radius:2px}
.btn-red{left:210px;width:95px;background:var(--red);box-shadow:0 2px 0 #7d0f10}
.btn-dark{left:352px;width:95px;background:#3b3b3b;box-shadow:0 2px 0 #1e1e1e}
.or{left:313px;top:236px;font-size:10px;color:#444}
.arrow{top:178px;width:26px;height:26px;border-radius:50%;background:#fff;display:flex;align-items:center;justify-content:center}
.arrow svg{width:8px;height:8px;stroke:#555;stroke-width:2;fill:none}

/* sections */
.section-title{left:0;width:651px;text-align:center;font-size:22px;color:#444;font-weight:400}
.section-title em{font-style:normal;color:var(--red);font-weight:700}
.cred-icon{width:65px;height:65px;border-radius:50%;display:flex;align-items:center;justify-content:center}
.cred h3{font-size:10px;font-weight:700;color:#555;margin-bottom:9px}
.cred p{font-size:8.8px;line-height:13.3px;color:#555;width:238px}

.col-head{font-size:13px;color:#333;display:flex;align-items:center;gap:10px}
.col-head::after{content:"";flex:1;height:1px;background:var(--rule)}
.blog-list{left:12px;top:786px;width:225px}
.blog-item{height:21px;border:1px solid #dcdcdc;background:#f7f7f7;font-size:9px;line-height:19px;padding-left:5px;margin-bottom:4px;position:relative}
.blog-item::after{content:"+";position:absolute;right:6px;top:0;color:#999;font-weight:700}
.tweet{display:flex;gap:12px;padding:5px 0 4px 10px;border-bottom:2px solid #eee;height:63px}
.tweet i{width:25px;height:25px;flex:none;margin-top:5px;display:block}
.tweet p{font-size:8.5px;line-height:12.5px;color:#555}
.tweet p a{color:var(--link);text-decoration:none}
.tweet p small{display:block;color:#bbb;font-size:8.5px}
.photo{width:86px;height:64px;border:3px solid #ddd}

/* footer */
.footer{left:0;top:966px;width:651px;height:181px;background:var(--foot);color:#999}
.footer h4{font-size:12.5px;color:#fff;font-weight:400;position:absolute;top:23px}
.footer p{font-size:7.5px;line-height:11px;color:#8a8a8a}
.portrait{left:21px;top:56px;width:89px;height:95px;border:3px solid #ccc;background:linear-gradient(160deg,#6a5446,#b98f78 55%,#e8dcd2)}
.role{left:117px;top:56px;font-size:11px;color:#fff}
.details{left:118px;top:73px;font-size:7.5px;line-height:11px;color:#8a8a8a}
.select{left:462px;top:110px;width:155px;height:17px;background:#5b5b5b;border:1px solid #666;font-size:7px;color:#ddd;padding-left:6px;line-height:15px}
.select::after{content:"";position:absolute;right:6px;top:5px;border:4px solid transparent;border-top:5px solid #bbb}
.bottom{left:0;top:1147px;width:651px;height:53px;background:var(--foot-deep)}
.bottom span{position:absolute;left:25px;top:21px;font-size:8.5px;color:#999}
.badges{position:absolute;right:42px;top:15px;display:flex;gap:4px;align-items:center}
.badges i{width:19px;height:19px;border-radius:50%;display:block}
.badges .house{width:20px;height:20px;border-radius:0;background:#ccc;margin-right:6px}
</style>
</head>
<body>
<div class="sheet">
  <header>
    <div class="abs brand">Marisol Kettering</div>
    <div class="abs brand-sub">The Marisol Kettering Team</div>
    <div class="abs partner"><b>Brookvale Funding</b><i></i></div>
    <div class="abs partner-sub">A Ridgeline Capital Company.</div>
    <div class="abs contact">
      <span><svg viewBox="0 0 10 10"><path d="M0 2h10v6H0z"/></svg>email@example.com</span>
      <span><svg viewBox="0 0 10 10"><path d="M2 0l2 3-1 1q1 2 3 3l1-1 3 2-1 2Q3 10 0 2z"/></svg>+00 (123) 456 78 90</span>
    </div>
  </header>

  <nav class="abs nav">
    <a>Home</a><a>About</a><a>Builders</a><a>Mortage Info</a><a>Approval</a><a>Blog</a><a>Contact</a>
    <div class="nav-social"><i></i><i></i><i></i></div>
  </nav>

  <section class="abs hero" role="img" aria-label="Blurred photo of two business people walking through a bright office corridor">
    <div class="abs arrow" style="left:12px"><svg viewBox="0 0 8 8"><path d="M5 1L2 4l3 3"/></svg></div>
    <div class="abs arrow" style="right:12px"><svg viewBox="0 0 8 8"><path d="M3 1l3 3-3 3"/></svg></div>
    <h1 class="abs hero-title">Earning Your Business</h1>
    <p class="abs hero-text">The Marisol Kettering Team relies on strong systems to deliver on-time, done-right and friendly eperience</p>
    <div class="abs btn btn-red">Start Here</div>
    <div class="abs or">– Or –</div>
    <div class="abs btn btn-dark">Get to Know Us</div>
  </section>

  <h2 class="abs section-title" style="top:525px">Our <em>Credentials</em></h2>
  <div class="abs cred-icon" style="left:12px;top:580px;background:#eee">
    <svg width="24" height="22" viewBox="0 0 24 22" fill="#666"><rect x="1" y="2" width="6" height="20"/><rect x="9" y="8" width="6" height="14"/><rect x="17" y="12" width="6" height="10"/></svg>
  </div>
  <div class="abs cred" style="left:89px;top:581px">
    <h3>Awards</h3>
    <p>Lorem Ipsum is simply dummy text of the printing and typesetting industry. Lorem Ipsum has been the industry's standard dummy text ever since the 1500s been</p>
  </div>
  <div class="abs cred-icon" style="left:337px;top:580px;background:var(--red)">
    <svg width="26" height="22" viewBox="0 0 26 22" fill="none" stroke="#fff" stroke-width="3.5"><path d="M3 11l7 7L23 3"/></svg>
  </div>
  <div class="abs cred" style="left:415px;top:581px">
    <h3>Recognition</h3>
    <p>Lorem Ipsum is simply dummy text of the printing and typesetting industry. Lorem Ipsum has been the industry's standard dummy text ever since the 1500s been</p>
  </div>

  <h2 class="abs section-title" style="top:690px">Engaged in our <em>Community</em></h2>

  <div class="abs col-head" style="left:16px;top:752px;width:221px">Blog</div>
  <div class="abs blog-list">
    <div class="blog-item">Borrowing</div>
    <div class="blog-item">Best Practices</div>
    <div class="blog-item">Announcements</div>
    <div class="blog-item">Resources</div>
    <div class="blog-item">How to guides</div>
    <div class="blog-item">Builders info</div>
  </div>

  <div class="abs col-head" style="left:257px;top:754px;width:180px">Social</div>
  <div class="abs" style="left:247px;top:776px;width:190px">
    <div class="tweet"><i style="background:#2fa6dd"></i><p><a>@kettering_team</a> Lorem Ipsum is the dummy text the printing typesetting instry Ipsum is has been.Lorem<small>3 days ago</small></p></div>
    <div class="tweet"><i style="background:#3b5b9a"></i><p><a>@kettering_team</a> Lorem Ipsum is the dummy text the printing typesetting instry Ipsum is has been.Lorem<small>3 days ago</small></p></div>
    <div class="tweet" style="border:none"><i style="background:#d64537"></i><p><a>@kettering_team</a> Lorem Ipsum is the dummy text the printing typeset-<small>3 days ago</small></p></div>
  </div>

  <div class="abs col-head" style="left:462px;top:754px;width:178px">In the Community</div>
  <div class="abs photo" role="img" aria-label="Community photo: businessman in an office" style="left:463px;top:791px;background:linear-gradient(135deg,#d6dde3,#7d8894)"></div>
  <div class="abs photo" role="img" aria-label="Community photo: smiling team member" style="left:556px;top:791px;background:linear-gradient(135deg,#eef0f2,#a7a9ab)"></div>
  <div class="abs photo" role="img" aria-label="Community photo: senior team member portrait" style="left:463px;top:865px;background:linear-gradient(135deg,#5c5f63,#c49a86)"></div>
  <div class="abs photo" role="img" aria-label="Community photo: team member by a window" style="left:556px;top:865px;background:linear-gradient(135deg,#cfe0ea,#3e4a5e)"></div>

  <footer class="abs footer">
    <h4 style="left:21px">About Marisol Kettering</h4>
    <div class="abs portrait" role="img" aria-label="Portrait of Marisol Kettering, branch manager"></div>
    <div class="abs role">Branch Manager</div>
    <div class="abs details">Office: 555.010.2200<br>Cell: 555.010.4471<br>mkettering@brookvale.example<br>NMLS: 40219<br>2140 Maple Crossing, Ste.210<br>Plano, TX 75024<br>Directions</div>

    <h4 style="left:259px">Disclaimer</h4>
    <p class="abs" style="left:260px;top:60px;width:160px">In accordance with Section 326 of the USA PATRIOT Act of 2001, Brookvale Funding is required to obtain a copy of the documents used in identifying our new account customers. This notice is being provided to you for adequate notice given under this act.</p>

    <h4 style="left:462px">Language</h4>
    <p class="abs" style="left:462px;top:60px;width:155px">Lorem Ipsum is simply dummy text of the printing and typesetting industry. Lorem Ipsum has been the industry's standard dummy text ever since the 1500s been the</p>
    <div class="abs select">English</div>
  </footer>

  <div class="abs bottom">
    <span>Marisol Kettering • Legal</span>
    <div class="badges">
      <i class="house"></i>
      <i style="background:#5d9fc4"></i>
      <i style="background:#3e5b98"></i>
      <i style="background:#d97b27"></i>
    </div>
  </div>
</div>
</body>
</html>
```